Herbal Apothecary Rebrand

I am in the process of merging two companies Fern Hollow Oils and Under Willow Apothecary. I am dissolving Fern Hollow Oils (FHO) and need to blend a few of the products into the Under Willow Apothecary (UWA) line. These blended products will take on a fresh new look. This is where I need some help. I have a few ideas but need some creative genius to bring them together.
The following products need to be merged and once a logo is agreed upon I will be working with this designer with further pay to create the following:
~ body oils (labels and packaging) **existing product shown in image A-1
~ plant bath medicines (labels and packaging) **a new product with the bottle and packaging shown in images attached
~ facial serum (labels and packaging - the packaging will be the same cardboard boxes used for the body oils) **existing product shown in
image A-2
~ teas (labeling) **a new product - packaging sample pics attached
~ as well as having the ability to carry over into the creation of 40 different essential oil containers. ** An idea I have is shown in image C-1.
Ideas...
I prefer distinct lines, square designs vs circular or curvy. I prefer clean and clear vs busy.
I like the layout shown in images A-1 & A-2 and could see moving forward with a very similar style without the indigenous logo. I would like to see what it looks like to have the UWA logo (building with trees) in place of the indigenous logo. ** I am open to reworking the UWA logo to make it a bit more vertical in size vs being quite small and horizontal. This could include revising or recreating the building and trees altogether.
I like the speckled background (shown in image B-1), it gives the sense that it is aged and goes with the Apothecary theme, however I'm not completely attached to it.
I like the off white labels that I currently have for the BODY OILS and the SERUM and I am leaning towards this as the colour for the new blended line. I would also be open to seeing a lighter version of the turquoise.
This is just an idea that I have however I am open to something completely new. What is important is that it blends nicely with the current line of products available at UWA (the entire line can be seen online). There is a good chance that I will be merging the products over to the new and improved design as we move through the older packaging.
Notes on Plant Bath labels:
**If working from the current layout of the Body Oil labels this can be used as an example to create a template
~ The top will have the new or reworked logo (with or without the company name depending on space available)
~ First line for each bottle will have a name eg: NETTLE + ROSE
~ Second line will be the purpose of the medicine eg: HEART OPENING
~ The next line will read: PLANT BATH
~Then space for a little blurb eg: BRINGING BALANCE TO THE EMOTIONAL AND ENERGETIC HEALTH OF THE HEART.
~ The size of the bottle will read 400 ML but in a vertical direction on the bottle
Notes on Tea labels:
The teas have not been created yet but I'm looking for some ideas that follow in the same design as the Plant Bath labels so the following can be used as an example:
~ Name; TULSI + ROSE
~ The purpose: ELEVATED HEART
~ The bottom will read: LOOSE TEA
~ Blurb about the benefits: A TRANSFORMATIONAL CREATION OF WARM NOTES WITH DEEP WOODY UNDERTONES. THIS ANYTIME TEA IS AS PLEASING IN THE HEALTH BENEFITS AS IT IS TO THE TASTE.
~ Include the size: 100g
**I maxed out in pictures so I wasn't able to add more inspiration pics but I also quite like the brook & meadow tea line (shows up in a google search) as its clean and clear. The difference being I won't be printing directly on the packaging, it will need to be a label.
Logo Text
I would like to see if we can incorporate the name UNDER WILLOW APOTHECARY however this might make it too busy. Perhaps smaller lettering for "under willow" and larger for "APOTHECARY". It also might be the case that adding this on the front makes things look too busy. I'm open to creative suggestions.

```html
<!DOCTYPE html>
<html lang="en">
<head>
<meta charset="utf-8">
<title>Under Willow Apothecary – Product Labels</title>
<link href="https://fonts.googleapis.com/css2?family=Antonio:wght@300;400;600;700&family=Roboto:wght@300&display=swap" rel="stylesheet">
<style>
  :root {
    --ink: #6c2819;
    --paper: #f0efed;
    --paper-shade: #e6e4e1;
    --art: #c9b3ad;
    --page: #ffffff;
  }
  * { margin: 0; padding: 0; box-sizing: border-box; }
  html, body {
    width: 1000px; height: 1200px; overflow: hidden;
    background: var(--page);
  }
  .sheet { position: relative; width: 1000px; height: 1200px; }

  .label {
    position: absolute; left: 128px; width: 717px; height: 520px;
    background:
      radial-gradient(circle at 20% 30%, var(--paper-shade) 0, transparent 40%),
      radial-gradient(circle at 80% 75%, var(--paper-shade) 0, transparent 45%),
      var(--paper);
    overflow: hidden;
  }
  .label--tea { top: 44px; }
  .label--bath { top: 619px; }
  .label svg { display: block; width: 717px; height: 520px; }

  .ink { fill: var(--ink); font-family: "Antonio", sans-serif; }
  .usage { font-size: 11.5px; font-weight: 300; }
  .usage tspan.lead { font-weight: 600; }
  .brand-name { font-size: 21px; font-weight: 400; }
  .product-name { font-size: 66px; font-weight: 600; }
  .product-name--bold { font-weight: 700; }
  .product-type { font-size: 47px; font-weight: 600; }
  .product-line { font-size: 41px; font-weight: 400; }
  .blurb { font-size: 22px; font-weight: 300; }
  .net-size { font-size: 31px; font-weight: 700; }
  .web-address { fill: var(--ink); font-family: "Roboto", sans-serif; font-size: 20px; font-weight: 300; }
  .rule { fill: var(--ink); }
  .web-panel { fill: none; stroke: var(--ink); stroke-width: 1; }
  .brand-art { fill: var(--art); }
</style>
</head>
<body>
<main class="sheet">

  <section class="label label--tea">
    <svg viewBox="0 0 717 520" aria-label="Tulsi + Rose loose tea label">
      <g class="ink usage">
        <text transform="translate(48 482) rotate(-90)" textLength="426" lengthAdjust="spacingAndGlyphs"><tspan class="lead">SUGGESTED USE:</tspan> WARM OIL IF DESIRED. APPLY TO THE FULL BODY AFTER BATHING.</text>
        <text transform="translate(63 482) rotate(-90)" textLength="440" lengthAdjust="spacingAndGlyphs">MASSAGE IN MOTIONS TOWARD THE HEART UNTIL THE OIL IS MOSTLY ABSORBED. CAN</text>
        <text transform="translate(79 482) rotate(-90)" textLength="166" lengthAdjust="spacingAndGlyphs">ALSO BE ADDED TO BATH WATER.</text>
        <text transform="translate(107 482) rotate(-90)" textLength="424" lengthAdjust="spacingAndGlyphs"><tspan class="lead">INGREDIENTS:</tspan> SUNFLOWER OIL, ORANGE, CARDAMOM, CYPRESS, GINGER ORGANIC.</text>
      </g>

      <text class="ink brand-name" x="359" y="70" text-anchor="middle" textLength="230" lengthAdjust="spacingAndGlyphs">UNDER WILLOW APOTHECARY</text>
      <rect class="brand-art" x="271" y="87" width="176" height="63" role="img" aria-label="Illustration of a small cabin among pine trees"/>

      <text class="ink product-name" x="204" y="244" textLength="309" lengthAdjust="spacingAndGlyphs">TULSI + ROSE</text>
      <rect class="rule" x="203" y="263" width="313" height="2"/>
      <text class="ink product-type" x="204" y="311" textLength="184" lengthAdjust="spacingAndGlyphs">LOOSE TEA</text>
      <rect class="rule" x="203" y="320" width="313" height="2"/>
      <text class="ink product-line" x="204" y="369" textLength="308" lengthAdjust="spacingAndGlyphs">ORGANIC BOTANICALS</text>
      <rect class="rule" x="203" y="390" width="313" height="2"/>

      <text class="ink blurb" x="204" y="424" textLength="169" lengthAdjust="spacingAndGlyphs">A TRANSFORMATIONAL</text>
      <text class="ink blurb" x="204" y="447" textLength="205" lengthAdjust="spacingAndGlyphs">CREATION OF WARM NOTES</text>
      <text class="ink blurb" x="204" y="469" textLength="254" lengthAdjust="spacingAndGlyphs">WITH DEEP WOODY UNDERTONES.</text>
      <rect class="rule" x="465" y="403" width="1.5" height="66"/>
      <text class="ink net-size" transform="translate(503 466) rotate(-90)" textLength="50" lengthAdjust="spacingAndGlyphs">100g</text>
      <rect class="rule" x="203" y="481" width="313" height="2"/>

      <rect class="web-panel" x="580.5" y="45.5" width="105" height="437"/>
      <text class="web-address" transform="translate(673 372) rotate(-90)" textLength="222" lengthAdjust="spacingAndGlyphs">underwillowapothecary.com</text>
    </svg>
  </section>

  <section class="label label--bath">
    <svg viewBox="0 0 717 520" aria-label="Nettle + Rose plant bath label">
      <g class="ink usage">
        <text transform="translate(48 482) rotate(-90)" textLength="426" lengthAdjust="spacingAndGlyphs"><tspan class="lead">SUGGESTED USE:</tspan> WARM OIL IF DESIRED. APPLY TO THE FULL BODY AFTER BATHING.</text>
        <text transform="translate(63 482) rotate(-90)" textLength="440" lengthAdjust="spacingAndGlyphs">MASSAGE IN MOTIONS TOWARD THE HEART UNTIL THE OIL IS MOSTLY ABSORBED. CAN</text>
        <text transform="translate(79 482) rotate(-90)" textLength="166" lengthAdjust="spacingAndGlyphs">ALSO BE ADDED TO BATH WATER.</text>
        <text transform="translate(107 482) rotate(-90)" textLength="424" lengthAdjust="spacingAndGlyphs"><tspan class="lead">INGREDIENTS:</tspan> SUNFLOWER OIL, ORANGE, CARDAMOM, CYPRESS, GINGER ORGANIC.</text>
      </g>

      <text class="ink brand-name" x="359" y="70" text-anchor="middle" textLength="230" lengthAdjust="spacingAndGlyphs">UNDER WILLOW APOTHECARY</text>
      <rect class="brand-art" x="271" y="87" width="176" height="63" role="img" aria-label="Illustration of a small cabin among pine trees"/>

      <text class="ink product-name product-name--bold" x="207" y="244" textLength="298" lengthAdjust="spacingAndGlyphs">NETTLE + ROSE</text>
      <rect class="rule" x="203" y="263" width="313" height="2"/>
      <text class="ink product-type" x="204" y="311" textLength="211" lengthAdjust="spacingAndGlyphs">PLANT BATH</text>
      <rect class="rule" x="203" y="320" width="313" height="2"/>
      <text class="ink product-line" x="204" y="369" textLength="308" lengthAdjust="spacingAndGlyphs">ORGANIC BOTANICALS</text>
      <rect class="rule" x="203" y="390" width="313" height="2"/>

      <text class="ink blurb" x="204" y="424" textLength="169" lengthAdjust="spacingAndGlyphs">A TRANSFORMATIONAL</text>
      <text class="ink blurb" x="204" y="447" textLength="205" lengthAdjust="spacingAndGlyphs">CREATION OF WARM NOTES</text>
      <text class="ink blurb" x="204" y="469" textLength="254" lengthAdjust="spacingAndGlyphs">WITH DEEP WOODY UNDERTONES.</text>
      <rect class="rule" x="465" y="403" width="1.5" height="66"/>
      <text class="ink net-size" transform="translate(503 467) rotate(-90)" textLength="66" lengthAdjust="spacingAndGlyphs">400ML</text>
      <rect class="rule" x="203" y="481" width="313" height="2"/>

      <rect class="web-panel" x="580.5" y="45.5" width="105" height="437"/>
      <text class="web-address" transform="translate(673 372) rotate(-90)" textLength="222" lengthAdjust="spacingAndGlyphs">underwillowapothecary.com</text>
    </svg>
  </section>

</main>
</body>
</html>
```